High Tech Real Estate Startup needs a business card

We are developing an innovative real estate marketing product based around advanced search and virtual reality.

We talk to people, we need business cards.

Target Market(s)

The target market is technology professionals and realtors.

Contact Information for Business Card

The information to be included will include

Name
Title
Phone Number
E-mail Address
www.zelquin.com

It should use simple iconography for each one of those fields.

Font styles to use
Other font styles liked:
• Co, Jubilat, Avenir

Colors

Designer to choose colors to be used in the design.

Requirements
Must have
• Clean aesthetic,
• Good use of negative space.
• It should use our company logo, shown in the attached file. It is able to use the negative of that logo (coloured font and white background) and I have attached other acceptable accent colours in a swatch file.
Should not have
• Should not be too busy
• No extraneous text (slogans, tag lines etc)

```html
<!DOCTYPE html>
<html lang="en">
<head>
<meta charset="utf-8">
<title>Zelquin Business Card</title>
<link href="https://fonts.googleapis.com/css2?family=Work+Sans:wght@400;500&display=swap" rel="stylesheet">
<style>
  :root {
    --backdrop: #3a3a3c;
    --card-white: #ffffff;
    --card-shade: #ececec;
    --card-dark: #1f1f20;
    --teal: #17a9ae;
    --teal-bright: #1fc0c6;
    --ink: #1b1b1b;
    --pattern-line: #4a4a4c;
  }
  * { box-sizing: border-box; margin: 0; padding: 0; }
  html, body { width: 1200px; height: 900px; overflow: hidden; }
  body {
    background: var(--backdrop);
    font-family: "Work Sans", sans-serif;
    position: relative;
  }
  .card {
    position: absolute;
    left: 280px;
    width: 640px;
    height: 366px;
    border-radius: 22px;
    overflow: hidden;
  }
  .card-front {
    top: 60px;
    background: radial-gradient(circle at 60% 40%, var(--card-white) 0%, var(--card-white) 45%, var(--card-shade) 100%);
  }
  .card-back {
    top: 474px;
    background: var(--card-dark);
  }
  .front-band { position: absolute; left: 0; bottom: 0; width: 640px; height: 40px; }
  .wordmark {
    position: absolute;
    font-family: "Work Sans", sans-serif;
    font-weight: 500;
    color: var(--teal);
    letter-spacing: 3px;
  }
  .card-front .wordmark { left: 40px; top: 128px; font-size: 60px; }
  .divider {
    position: absolute;
    left: 338px; top: 92px;
    width: 2px; height: 170px;
    background: var(--teal-bright);
  }
  .contact {
    position: absolute;
    left: 362px; top: 98px;
    color: var(--ink);
    font-size: 15px;
    line-height: 1.32;
  }
  .contact-name {
    color: var(--teal-bright);
    font-size: 19px;
    font-weight: 500;
    text-transform: uppercase;
    line-height: 1.15;
  }
  .contact-row { display: flex; align-items: center; gap: 8px; }
  .contact-row svg { width: 12px; height: 12px; flex: none; }
  .contact-address { margin-bottom: 2px; }
  .back-pattern { position: absolute; inset: 0; background: linear-gradient(135deg, #242425 0%, #1c1c1d 100%); }
  .card-back .wordmark { left: 50%; top: 50%; transform: translate(-50%, -50%); font-size: 64px; }
</style>
</head>
<body>
  <section class="card card-front">
    <div class="wordmark">ZELQUIN</div>
    <div class="divider"></div>
    <div class="contact">
      <div class="contact-name">Daniel Harlow</div>
      <div class="contact-title">Director</div>
      <div class="contact-address">416 Maple Ridge Ln.<br>Franklin, TN 37064</div>
      <div class="contact-row">
        <svg viewBox="0 0 12 12"><path d="M3 1 L5 3.5 L4 4.8 Q5 7 7.2 8 L8.5 7 L11 9 L9.8 10.8 Q4.5 10.5 1.2 3 Z" fill="none" stroke="var(--teal)" stroke-width="1.1"/></svg>
        <span>+1-555-210-7381</span>
      </div>
      <div class="contact-row">
        <svg viewBox="0 0 12 12"><rect x="1" y="2.5" width="10" height="7" fill="none" stroke="var(--teal)" stroke-width="1.1"/><path d="M1 2.5 L6 6.5 L11 2.5" fill="none" stroke="var(--teal)" stroke-width="1.1"/></svg>
        <span>info@zelquin.com</span>
      </div>
      <div class="contact-row">
        <svg viewBox="0 0 12 12"><circle cx="6" cy="6" r="5" fill="none" stroke="var(--teal)" stroke-width="1.1"/><ellipse cx="6" cy="6" rx="2.2" ry="5" fill="none" stroke="var(--teal)" stroke-width="0.9"/><path d="M1 6 H11" stroke="var(--teal)" stroke-width="0.9"/></svg>
        <span>www.zelquin.com</span>
      </div>
    </div>
    <svg class="front-band" viewBox="0 0 640 40" preserveAspectRatio="none">
      <polygon points="0,0 200,0 188,40 0,40" fill="var(--card-dark)"/>
      <polygon points="212,14 640,14 640,40 204,40" fill="var(--teal-bright)"/>
    </svg>
  </section>

  <section class="card card-back">
    <div class="back-pattern" role="img" aria-label="Faint network of connected dots and lines across the dark card face"></div>
    <div class="wordmark">ZELQUIN</div>
  </section>
</body>
</html>
```